Hot Pilates studio needs window graphics/ front signage

We need window graphics for the front of our hot pilates studio. We have several large front windows that are visible from the street and would be beneficial to have signage. Glow Loft offers several different heated classes on the mat including: Hot Pilates, Sculpt, Hot Barre. I would like for people that drive by to know what we are. The window dimensions are (4 windows) 41 inches X 61 inches, (4 windows) 34 inches X 61 inches (a total of 8 window panels)

Target Market(s)

fit women and men ages 16-65

Industry/Entity Type

fitness, pilates,

Font styles to use
Sans Serif

Colors

Designer to choose only greyscale colors for use in the design.

Requirements
Must have
• HOT PILATES
Nice to have
• our hashtag is #StayRadiant

```html
<!DOCTYPE html>
<html lang="en">
<head>
<meta charset="utf-8">
<title>Glow Loft – Window Graphics</title>
<link rel="stylesheet" href="https://fonts.googleapis.com/css2?family=Oswald:wght@200;300;500&display=swap">
<style>
  :root {
    --bg-dark: #1c1c1c;
    --bg-light: #9a9a9a;
    --panel-light: #e4e4e4;
    --panel-lighter: #f4f4f4;
    --photo-tone-a: #8d8a86;
    --photo-tone-b: #4c4a4a;
    --frame-white: #ffffff;
    --block-black: #1d1d1d;
    --band-grey: #3b3b3b;
    --text-white: #ffffff;
  }
  * { margin: 0; padding: 0; box-sizing: border-box; }
  html, body { width: 945px; height: 1200px; overflow: hidden; }
  body {
    background: linear-gradient(115deg, var(--bg-dark) 0%, #3a3a3a 45%, var(--bg-light) 100%);
    font-family: "Oswald", "Arial Narrow", sans-serif;
    color: var(--text-white);
  }
  .panel-row {
    position: absolute;
    top: 425px;
    left: 28px;
    display: flex;
    gap: 24px;
  }
  .window-panel {
    position: relative;
    width: 204px;
    height: 349px;
    box-shadow: 0 6px 14px rgba(0,0,0,0.45);
  }
  .window-panel svg { position: absolute; inset: 0; width: 100%; height: 100%; }
  .class-title {
    position: absolute;
    left: 27px;
    bottom: 63px;
    font-size: 28px;
    line-height: 1.04;
    text-transform: uppercase;
    letter-spacing: 0.2px;
  }
  .class-title .thin { font-weight: 200; display: block; }
  .class-title .bold { font-weight: 500; display: block; }
  .class-title.offset-left { left: 25px; }
  .contact-line {
    position: absolute;
    left: 0; right: 0;
    bottom: 16px;
    text-align: center;
    font-size: 11.5px;
    font-weight: 300;
    letter-spacing: 0.2px;
    text-transform: uppercase;
  }
  .social-mark {
    display: inline-block;
    width: 11px; height: 11px;
    border: 1px solid var(--text-white);
    border-radius: 50%;
    vertical-align: -1px;
    margin-left: 4px;
  }
</style>
</head>
<body>
<svg width="0" height="0" style="position:absolute">
  <defs>
    <linearGradient id="panelBackdrop" x1="0" y1="0" x2="1" y2="1">
      <stop offset="0" stop-color="var(--panel-lighter)"/>
      <stop offset="0.5" stop-color="var(--panel-light)"/>
      <stop offset="1" stop-color="var(--panel-lighter)"/>
    </linearGradient>
    <linearGradient id="photoTone" x1="0" y1="0" x2="0" y2="1">
      <stop offset="0" stop-color="var(--photo-tone-a)"/>
      <stop offset="1" stop-color="var(--photo-tone-b)"/>
    </linearGradient>
  </defs>
</svg>

<main class="panel-row">
  <section class="window-panel">
    <svg viewBox="0 0 330 565" preserveAspectRatio="none">
      <rect width="330" height="565" fill="url(#panelBackdrop)"/>
      <polygon points="55,165 125,0 330,0 330,300 285,342 150,342" fill="url(#photoTone)" stroke="var(--frame-white)" stroke-width="7" role="img" aria-label="Photo of an instructor holding a pilates ring in a boat pose on a mat"/>
      <path d="M0 312 L55 280 Q70 272 85 278 L292 382 Q302 388 302 402 L302 492 L0 492 Z" fill="var(--block-black)"/>
      <path d="M0 492 L330 480 L330 565 L0 565 Z" fill="var(--band-grey)"/>
    </svg>
    <h2 class="class-title"><span class="thin">Hot</span><span class="bold">Cardio</span><span class="thin">Pilates</span></h2>
    <p class="contact-line">www.glowloftstudio.com</p>
  </section>

  <section class="window-panel">
    <svg viewBox="0 0 330 565" preserveAspectRatio="none">
      <rect width="330" height="565" fill="url(#panelBackdrop)"/>
      <polygon points="55,165 125,0 330,0 330,300 285,342 150,342" fill="url(#photoTone)" stroke="var(--frame-white)" stroke-width="7" role="img" aria-label="Photo of a class on hands and knees doing a mat exercise"/>
      <path d="M0 312 L55 280 Q70 272 85 278 L292 382 Q302 388 302 402 L302 492 L0 492 Z" fill="var(--block-black)"/>
      <path d="M0 492 L330 480 L330 565 L0 565 Z" fill="var(--band-grey)"/>
    </svg>
    <h2 class="class-title offset-left"><span class="thin">Total</span><span class="bold">Body Burn</span></h2>
    <p class="contact-line">305-555-0142</p>
  </section>

  <section class="window-panel">
    <svg viewBox="0 0 330 565" preserveAspectRatio="none">
      <rect width="330" height="565" fill="url(#panelBackdrop)"/>
      <polygon points="55,165 125,0 330,0 330,300 285,342 150,342" fill="url(#photoTone)" stroke="var(--frame-white)" stroke-width="7" role="img" aria-label="Photo of an instructor stretching at the barre"/>
      <path d="M0 312 L55 280 Q70 272 85 278 L292 382 Q302 388 302 402 L302 492 L0 492 Z" fill="var(--block-black)"/>
      <path d="M0 492 L330 480 L330 565 L0 565 Z" fill="var(--band-grey)"/>
    </svg>
    <h2 class="class-title"><span class="thin">Hot</span><span class="bold">Cardio</span><span class="thin">Barre</span></h2>
    <p class="contact-line">info@glowloftstudio.com</p>
  </section>

  <section class="window-panel">
    <svg viewBox="0 0 330 565" preserveAspectRatio="none">
      <rect width="330" height="565" fill="url(#panelBackdrop)"/>
      <polygon points="55,165 125,0 330,0 330,300 285,342 150,342" fill="url(#photoTone)" stroke="var(--frame-white)" stroke-width="7" role="img" aria-label="Photo of an instructor leaning forward in suspension straps"/>
      <path d="M0 312 L55 280 Q70 272 85 278 L292 382 Q302 388 302 402 L302 492 L0 492 Z" fill="var(--block-black)"/>
      <path d="M0 492 L330 480 L330 565 L0 565 Z" fill="var(--band-grey)"/>
    </svg>
    <h2 class="class-title"><span class="thin">Pilates</span><span class="bold">X Flex</span></h2>
    <p class="contact-line">Follow us @glowloft<span class="social-mark"></span></p>
  </section>
</main>
</body>
</html>
```